Business card for Luxury Portable Restroom Trailer company

We are a Luxury Portable Restroom Trailer Company Called FALCRIDGE HIRES. Based in Orange County California. We provide portable restroom trailers for events, such as, Weddings, Concerts, Charity events, Sporting events, Tournaments, Corporate events, ect. We rent and Sell the Luxury restrooms. Our colors are white, grey, and Orange. As you will see in the logo we uploaded.
There are 2 people in the company so the names and titles will change for the 3 people but card will remain the same. Here is the information for each Person: Dwight Penner CFO 555 318-0476
next Person: Leon Marchetti VP 555 318-0476
Next Person: Owen Marchetti CEO 555 318-0476
Information to include on the card: Luxury Restroom Trailers Rental and Sales. Weddings, Concerts, Charity, Sporting and Corp. Events.

```html
<!DOCTYPE html>
<html lang="en">
<head>
<meta charset="utf-8">
<title>Falcridge Hires – Business Card</title>
<link href="https://fonts.googleapis.com/css2?family=Montserrat:wght@400;600&family=Oswald:wght@500&display=swap" rel="stylesheet">
<style>
  :root {
    --orange: #f26f1e;
    --ink: #1f1f1f;
    --card-white: #ffffff;
    --card-grey: #4a4a4a;
    --backdrop: #d9d9d9;
  }
  * { box-sizing: border-box; margin: 0; padding: 0; }
  html, body { width: 1200px; height: 1200px; overflow: hidden; }
  body {
    background: var(--backdrop);
    display: flex;
    flex-direction: column;
    align-items: center;
    justify-content: center;
    gap: 60px;
    font-family: "Montserrat", sans-serif;
  }
  .card {
    width: 700px;
    height: 400px;
    border-radius: 30px;
    position: relative;
    overflow: hidden;
    border-bottom: 5px solid var(--orange);
    box-shadow: 0 6px 18px rgba(0,0,0,.18);
  }
  .card-front { background: var(--card-white); }
  .card-back { background: var(--card-grey); display: flex; align-items: center; justify-content: center; }

  .brand {
    display: flex;
    align-items: center;
    gap: 14px;
    color: var(--orange);
    font-weight: 600;
    font-size: 26px;
    letter-spacing: 1px;
  }
  .brand-dot {
    width: 26px; height: 26px;
    border-radius: 50%;
    background: var(--orange);
    flex: none;
  }
  .card-front .brand { position: absolute; top: 58px; right: 60px; }

  .person { position: absolute; left: 58px; top: 122px; }
  .person-name { color: var(--orange); font-weight: 600; font-size: 30px; letter-spacing: 1px; line-height: 1; }
  .person-title { color: var(--ink); font-size: 20px; margin-top: 4px; }
  .contact-list { list-style: none; margin-top: 12px; }
  .contact-list li {
    display: flex; align-items: center; gap: 12px;
    color: var(--ink); font-size: 18px; line-height: 30px;
  }
  .contact-list svg { width: 20px; height: 20px; flex: none; }

  .services {
    position: absolute; right: 40px; bottom: 28px;
    text-align: right;
    font-family: "Oswald", sans-serif;
    font-weight: 500;
    text-transform: uppercase;
    line-height: 1.15;
  }
  .services-main { color: var(--orange); font-size: 24px; }
  .services-events { color: var(--ink); font-size: 21px; }
  .services-events .bullet { color: var(--orange); padding: 0 4px; }

  .card-back .brand { font-size: 34px; gap: 18px; }
  .card-back .brand-dot { width: 34px; height: 34px; }
</style>
</head>
<body>
  <section class="card card-front">
    <div class="brand"><span class="brand-dot"></span>FALCRIDGE HIRES</div>

    <div class="person">
      <p class="person-name">DWIGHT PENNER</p>
      <p class="person-title">CFO</p>
      <ul class="contact-list">
        <li>
          <svg viewBox="0 0 24 24"><path fill="#f26f1e" d="M6.6 10.8a15.1 15.1 0 0 0 6.6 6.6l2.2-2.2c.3-.3.7-.4 1-.2 1.1.4 2.3.6 3.6.6.6 0 1 .4 1 1V20c0 .6-.4 1-1 1A17 17 0 0 1 3 4c0-.6.4-1 1-1h3.5c.6 0 1 .4 1 1 0 1.3.2 2.5.6 3.6.1.3 0 .7-.2 1z"/></svg>
          555 318-0476
        </li>
        <li>
          <svg viewBox="0 0 24 24"><rect x="2" y="5" width="20" height="14" rx="1" fill="#f26f1e"/><path d="M2 6l10 7 10-7" fill="none" stroke="#fff" stroke-width="1.6"/></svg>
          email@falcridgehires.com
        </li>
        <li>
          <svg viewBox="0 0 24 24" fill="none" stroke="#f26f1e" stroke-width="1.8"><circle cx="12" cy="12" r="9.5"/><ellipse cx="12" cy="12" rx="4.2" ry="9.5"/><path d="M2.5 12h19M4 7h16M4 17h16"/></svg>
          www.falcridgehires.com
        </li>
      </ul>
    </div>

    <div class="services">
      <p class="services-main">Luxury Restroom Trailers Rental and Sales.</p>
      <p class="services-events">Weddings<span class="bullet">•</span>Concerts<span class="bullet">•</span>Charity<span class="bullet">•</span>Sporting and Corp. Events.</p>
    </div>
  </section>

  <section class="card card-back">
    <div class="brand"><span class="brand-dot"></span>FALCRIDGE HIRES</div>
  </section>
</body>
</html>
```